Zielgruppe
Die Velorin Akademie bietet Kurse, Seminare & Coachings im Bereich der Kommunikation / Persönlichkeitsentwicklung an.
Folgendes Angebot besteht zur Zeit:
Seminare:
- 'Erste Schritte im Dialog', eine Einführung in die Kommunikation.
- 'Heitere Töchter, ruhige Väter' zum Thema Erziehung.
- 'Reifen mit Gelassenheit', zum Thema Älter werden und den Umgang damit.
Kurse:
- 'Gewaltfreie Kommunikation', Übungsgruppe
Coaching:
- Einzelsitzungen mit Hypnose
Ps: im Anhang unter 'Angabot_Vorlage.pdf' finden Sie mehr Infos zu den einezlenen Angebote.
Aufgabenstellung
Bitte berücksichtigen Sie, dass bereits ein Logo besteht (siehe Anhang).
Vom gesamteindruck her sollte die Website aufgeräumt, übersichtlich, harmonisch, freundlich & frisch wirken.
Es wäre super, wenn die Website authentisch wirkt (und weniger '0815 Business Website').
Bitte bedenken Sie, dass die Website sich an Private richtet, die sich nach einem 'strahlenderen & unbeschwerterem Lebene sehnen'.
Wir haben bereits viele Persönlichkeiten stärken können und möchten dies auch witerhin mit viel Herzblut machen.

```html
<!DOCTYPE html>
<html lang="de">
<head>
<meta charset="utf-8">
<title>Velorin Akademie – Startseite</title>
<link href="https://fonts.googleapis.com/css2?family=Montserrat:ital,wght@0,400;0,500;0,600;1,400&family=Raleway:wght@500;600&display=swap" rel="stylesheet">
<style>
:root{
  --canvas:#ede6df;
  --margin:#ffffff;
  --page:#ffffff;
  --nav:#ebe6dd;
  --plum:#5a4a6a;
  --ink:#4a4450;
  --muted:#6a6470;
  --coral:#f26a45;
  --apricot:#f1bc88;
  --card:#f3f0eb;
  --taupe:#9b8878;
  --line:#c9c2bb;
}
*{box-sizing:border-box;margin:0;padding:0}
html,body{width:1200px;height:2347px;overflow:hidden}
body{background:var(--canvas);font-family:"Montserrat",sans-serif;color:var(--ink);position:relative}
.side-margin{position:absolute;left:0;top:0;width:64px;height:2347px;background:var(--margin)}
.page{position:absolute;left:178px;top:68px;width:793px;height:2216px;background:var(--page)}
.abs{position:absolute}

/* nav */
.nav{left:0;top:0;width:793px;height:50px;background:var(--nav);border-bottom:1px solid #ddd6cc}
.nav-brand{left:27px;top:19px;font-size:8px;letter-spacing:1.5px;font-weight:500;color:#3b3540}
.nav-links{right:32px;top:17px;display:flex;gap:18px;font-size:7.5px;letter-spacing:.4px;color:#3b3540}
.nav-links span{padding:4px 8px}
.nav-links .active{border:1px solid var(--coral);color:var(--coral)}

/* hero */
.hero{left:0;top:50px;width:793px;height:419px;background:linear-gradient(180deg,#e6d3b6 0%,#f0c491 35%,#e9a070 55%,#9a7d8e 80%,#6f6384 100%)}
.hero-title{left:0;top:230px;width:793px;text-align:center;color:#fff;font-family:"Raleway",sans-serif;font-weight:500;font-size:33px;letter-spacing:4px}
.hero-sub{left:0;top:284px;width:793px;text-align:center;color:#fff;font-family:"Raleway",sans-serif;font-weight:600;font-size:16px;letter-spacing:1px}
.hero-arrow{top:170px}
.hero-dots{left:380px;top:392px;display:flex;gap:4px}
.hero-dots i{width:6px;height:6px;border-radius:50%;border:1px solid #fff;display:block}
.hero-dots i:first-child{background:#fff}

/* newsletter */
.newsletter{left:0;top:476px;width:793px;height:53px;background:var(--apricot)}
.newsletter-label{left:116px;top:14px;color:#fff;font-size:11px;line-height:13px}
.newsletter-label b{font-weight:600;letter-spacing:1.2px;font-size:10.5px}
.newsletter-input{left:344px;top:13px;width:280px;height:27px;background:#fff;border:1px solid #d8cfc4;font-size:9.5px;letter-spacing:1px;color:#9a929a;padding:8px 10px}
.newsletter-ok{left:636px;top:18px;width:34px;height:18px;background:var(--coral);color:#fff;font-size:9.5px;letter-spacing:1px;text-align:center;line-height:18px}

/* about */
.about-title{left:116px;top:580px;font-family:"Raleway",sans-serif;font-weight:600;font-size:22px;letter-spacing:.6px;color:var(--plum)}
.about-photo{left:116px;top:640px;width:226px;height:196px;background:linear-gradient(135deg,#e4e6e3,#d3d6d2 60%,#c9c6bd)}
.about-text{left:381px;top:640px;width:326px;font-size:9.6px;line-height:11.5px;color:var(--muted);text-align:justify}
.about-text p{margin-bottom:11px}
.btn{background:var(--coral);color:#fff;text-align:center;font-weight:500;letter-spacing:1.2px}
.about-btn{left:381px;top:808px;width:163px;height:28px;line-height:28px;font-size:10px}

/* offers */
.offers-banner{left:1px;top:905px;width:792px;height:153px;background:linear-gradient(180deg,#f5efe3 0%,#f7e6c8 55%,#f3d9b4 85%,#d7d0c8 100%)}
.offers-title{left:0;top:72px;width:792px;padding-left:50px;text-align:center;font-family:"Raleway",sans-serif;font-weight:600;font-size:22px;letter-spacing:.6px;color:var(--plum)}
.offer{left:1px;width:792px;height:165px;background:var(--card)}
.offer-photo{left:116px;top:18px;width:137px;height:124px}
.offer-body{left:286px;top:16px;width:421px}
.offer-title{font-size:11.5px;font-weight:600;color:var(--plum);letter-spacing:.2px;margin-bottom:12px}
.offer-text{font-size:7.6px;line-height:10.5px;color:var(--muted);text-align:justify}
.offer-text p{margin-bottom:11px}
.offer-text em{font-style:italic}
.offer-btn{left:286px;top:137px;width:52px;height:18px;line-height:18px;font-size:6.5px}

/* closing photo */
.closing-photo{left:1px;top:1632px;width:793px;height:222px;background:linear-gradient(180deg,#c7cbd3 0%,#e1dcd6 45%,#b9ab9e 70%,#5a4f4a 100%)}

/* footer */
.footer-brand{left:60px;top:1958px;width:216px;text-align:center;font-size:14px;letter-spacing:2px;color:#2f2b33}
.footer-address{left:60px;top:2006px;width:216px;text-align:center;font-size:11px;line-height:14px;color:var(--muted);font-style:normal}
.footer-address b{font-weight:600;color:var(--plum);letter-spacing:.4px;display:block;margin-bottom:14px}
.footer-address p{margin-bottom:13px}
.contact-title{left:414px;top:1879px;font-size:11px;line-height:14px;letter-spacing:.5px;color:var(--plum)}
.field{left:414px;width:279px;border:1px solid var(--line);background:#fff;font-size:9px;letter-spacing:1px;color:#a09aa0;padding:8px 9px}
.contact-send{left:416px;top:2092px;width:144px;height:27px;line-height:27px;font-size:10.5px}
.bottom-bar{left:1px;top:2149px;width:793px;height:67px;background:var(--taupe);color:#fff;font-size:11px;letter-spacing:.4px}
.bottom-bar span{position:absolute;top:27px}

/* annotation */
.annotation{left:1013px;top:1007px;width:167px;height:95px;background:#fff;font-size:11.5px;line-height:13px;color:#5b5a78;padding:20px 15px}
.annotation-arrow{left:973px;top:1043px}
</style>
</head>
<body>
<div class="side-margin"></div>

<main class="page">
  <header class="abs nav">
    <div class="abs nav-brand">VELORIN AKADEMIE</div>
    <nav class="abs nav-links"><span class="active">HOME</span><span>ANGEBOT</span><span>KONTAKT</span><span>ÜBER UNS</span></nav>
  </header>

  <section class="abs hero" role="img" aria-label="Foto: Hände formen vor der untergehenden Sonne einen Rahmen">
    <svg class="abs hero-arrow" style="left:18px" width="24" height="40" viewBox="0 0 24 40"><path d="M20 2 L4 20 L20 38" fill="none" stroke="#fff" stroke-width="2"/></svg>
    <svg class="abs hero-arrow" style="right:16px" width="24" height="40" viewBox="0 0 24 40"><path d="M4 2 L20 20 L4 38" fill="none" stroke="#fff" stroke-width="2"/></svg>
    <div class="abs hero-title">VELORIN AKADEMIE</div>
    <div class="abs hero-sub">NEUE PERSPEKTIVEN • NEUE HORIZONTE</div>
    <div class="abs hero-dots"><i></i><i></i><i></i></div>
  </section>

  <section class="abs newsletter">
    <div class="abs newsletter-label"><b>KOSTENLOSES ERSTGESPRÄCH</b><br>Abonnieren Sie unseren Newsletter!</div>
    <div class="abs newsletter-input">E-MAIL ADRESSE</div>
    <div class="abs newsletter-ok">OK</div>
  </section>

  <h2 class="abs about-title">CHANCE AUF EIN NEUES LEVEL ZU KOMMEN</h2>
  <div class="abs about-photo" role="img" aria-label="Porträtfoto einer Coachin in weißer Bluse"></div>
  <div class="abs about-text">
    <p>Lorem ipsum dolor sit amet, mea cu nihil torquatos. Ad error civibus vivendum nec. Antiopam praesent sea an, id nam alii facete elaboraret.</p>
    <p>Urbanitas adolescens vituperatoribus vel in. Lorem voluptua posidonium eu sea, esse fabellas cu eam, cu vim tation nusquam. Nostrum iudicabit vix et, tota vivendo nominati has cu.</p>
    <p>Lorem ipsum dolor sit amet, mea cu nihil torquatos. Ad error civibus vivendum nec. Antiopam praesent sea an, id nam alii facete elaboraret. Urbanitas adolescens vituperatoribus vel in. Lorem voluptua posidonium eu sea, esse fabellas cu eam.</p>
  </div>
  <div class="abs btn about-btn">MEHR ÜBER UNS</div>

  <section class="abs offers-banner" role="img" aria-label="Foto: Leuchtturm vor hellem Abendhimmel">
    <h2 class="abs offers-title">UNSERE AKTUELLE ANGEBOTE</h2>
  </section>

  <article class="abs offer" style="top:1084px">
    <div class="abs offer-photo" role="img" aria-label="Foto: Familie spaziert über eine Brücke" style="background:linear-gradient(135deg,#cfc9c0,#9d968d 60%,#7d776f)"></div>
    <div class="abs offer-body">
      <h3 class="offer-title">SEMINAR: Heitere Töchter, ruhige Väter</h3>
      <div class="offer-text">
        <p><em>„Unter Erziehung versteht man die pädagogische Einflussnahme auf die Entwicklung und das Verhalten Heranwachsender“.</em> Erziehungstheorien gibt es unzählige, die das Spektrum von streng und autoritär bis hin zum Laisser-faire decken. Das selbst erlebte wird z.T. auch unreflektiert wiederholt und/oder wir verlieren uns in unzählige Ratgeber.</p>
        <p>Mithilfe der Neurowissenschaften wird uns klar, dass das oft kräftezerrende Ringen rund um die Erziehung absolut unnötig und überflüssig ist, ja sogar schädigend.</p>
      </div>
    </div>
    <div class="abs btn offer-btn">MEHR</div>
  </article>

  <article class="abs offer" style="top:1262px">
    <div class="abs offer-photo" role="img" aria-label="Foto: Nahaufnahme eines Uhrwerks" style="background:linear-gradient(135deg,#8c8c8c,#dcdcdc 45%,#9a9a9a)"></div>
    <div class="abs offer-body">
      <h3 class="offer-title">SEMINAR: Zeit und Alternativen</h3>
      <div class="offer-text">
        <p>Zeit ist ein allgegenwärtiges (und manchmal leidiges) Thema, wie z.B „keine Zeit haben“ oder „die Zeit verfliegt im Nu“. Was IST jedoch Zeit? Wie und wo nehmen wir sie wahr? Welche Auswirkungen hat das „Zeit denken“? Was wäre, wenn wir der Zeit entkommen – aussteigen – könnten? Mit welchen Folgen? Welchen Zusammenhang haben Zeit und Alter?</p>
        <p><em>„Älter werden ist unumgänglich. Alt werden ist optional.“</em></p>
      </div>
    </div>
    <div class="abs btn offer-btn">MEHR</div>
  </article>

  <article class="abs offer" style="top:1441px">
    <div class="abs offer-photo" role="img" aria-label="Foto: Wendeltreppe von oben gesehen" style="background:radial-gradient(circle at 50% 60%,#5a5a5a 0,#bdbdbd 35%,#e6e6e6 70%)"></div>
    <div class="abs offer-body">
      <h3 class="offer-title">EINZELSITZUNGEN: Coaching mit Hypnose</h3>
      <div class="offer-text">
        <p>Einzelsitzungen...</p>
        <p>Hast du Lust, die Kraft deines Unterbewusstseins zu erfahren?<br>Hypnose macht es erlebbar und ermöglicht, Veränderungsarbeit (wie z.B. Verhalten, Rauchen, Phobien...) erfolgreich umzusetzen.</p>
      </div>
    </div>
    <div class="abs btn offer-btn">MEHR</div>
  </article>

  <div class="abs closing-photo" role="img" aria-label="Foto: Person sitzt auf einem Felsvorsprung über nebligen Bergen im Gegenlicht"></div>

  <div class="abs footer-brand">VELORIN AKADEMIE</div>
  <address class="abs footer-address">
    <b>VELORIN AKADEMIE GMBH.</b>
    <p>Lindenweg 12<br>4321 Beispieldorf</p>
    <p>TEL: 0176 987 654<br>info@velorin-akademie.ch</p>
  </address>

  <div class="abs contact-title">NOCH FRAGEN, ANREGUNGEN?<br>SCHREIBEN SIE UNS!</div>
  <div class="abs field" style="top:1919px;height:28px">NAME</div>
  <div class="abs field" style="top:1957px;height:28px">E-MAIL ADRESSE</div>
  <div class="abs field" style="top:1993px;height:87px">NACHRICHT</div>
  <div class="abs btn contact-send">SENDEN</div>

  <footer class="abs bottom-bar">
    <span style="left:48px">Datenschutz</span>
    <span style="left:150px">Impressum</span>
    <span style="left:337px">VELORIN AKADEMIE | 2019</span>
  </footer>
</main>

<svg class="abs annotation-arrow" width="40" height="12" viewBox="0 0 40 12"><path d="M0 6 H36" stroke="#333" stroke-width="1"/><path d="M32 2 L38 6 L32 10 Z" fill="#333"/></svg>
<aside class="abs annotation">Dieser Teil bleibt un­verändert, und die ak­tuellen Gebote werden sogar gescrollt</aside>
</body>
</html>
```